Site Redesign in WORDPRESS for a Aerial Survey Company

We are looking for an updated look to our website that reflects our aerial drone services. Our company is changing directions from helping to provide legal documentation for companies to operate UAVs for commercial operations, to now providing Aerial Data Collection services. We need the new website to focus on this new direction.

Wordpress Design (Uncoded - PSD layout only)

Current site: http://tornwickaviation.com/
Business card attached

VISUAL
********
The new pages should be visually top-notch, appealing, and more user-friendly to navigate, and represent our professionalism and level of expertise. We love the use of images, both great photography and technical. Our specialty is the use of Aerial LiDAR.

Our current site uses the Mallow template.

Colors: I've attached the Pantone for our logo colors

Fonts: Simple, clean and professional. We are not worried about specific fonts so long as they tie or compliment our logo.

STRUCTURE
****************
In the attached document I have laid out the pages we would like to have and the content outline of the content these pages will include.

We're happy to answer you questions in the comments and to provide quick feedback and additional info if necessary.

Target Market(s)

Agricultural and Engineering firms

Industry/Entity Type

Agribusiness

Coding

Coded - Design and coding required

Number of Pages Required

5+ page

Font styles to use
Sans Serif

Colors
0392cd
9bcb3c
ffffff

Requirements
Must have
• We need at a minimum a design with the Home/Landing, Services, and about. Need to be able to adapt the site as we add new services and increase our partnerships.
• Please provide in WordPress format.
• Links to social media: FB, TW, IG
Nice to have
• We like parrallax, but in the end it's about the overall feel of the site.
Should not have
• Please, professional designs only.

```html
<!DOCTYPE html>
<html lang="en">
<head>
<meta charset="utf-8">
<title>Tornwick Aviation</title>
<link rel="stylesheet" href="https://fonts.googleapis.com/css2?family=Raleway:wght@300;400;500;600;700&family=Open+Sans:wght@400;600&display=swap">
<style>
:root{
  --blue:#0392cd;
  --blue-light:#4a9fe0;
  --blue-deep:#2a7fd4;
  --green:#7cb518;
  --green-btn:#6bb024;
  --ink:#2b2b2b;
  --muted:#666;
  --line:#dedede;
  --footer:#383838;
  --footer-bottom:#2e2e2e;
  --white:#fff;
}
*{margin:0;padding:0;box-sizing:border-box}
html,body{width:1200px;height:3066px;overflow:hidden}
body{font-family:'Raleway',Arial,sans-serif;color:var(--ink);background:var(--white);position:relative}
section,header,footer{position:absolute;left:0;width:1200px}

/* header */
.site-header{top:0;height:98px;border-top:4px solid var(--blue);background:var(--white)}
.brand{position:absolute;left:98px;top:14px;display:flex;align-items:center;gap:10px;width:300px}
.brand-mark{width:62px;height:62px;background:var(--blue);flex:none}
.brand-name{font-weight:700;font-size:25px;color:var(--blue);line-height:25px;letter-spacing:1px}
.brand-tag{font-size:10px;color:var(--blue);margin-top:3px;white-space:nowrap}
.main-nav{position:absolute;left:482px;width:618px;top:46px;display:flex;justify-content:space-between;font-size:12.5px;font-weight:600;white-space:nowrap}
.main-nav a{color:var(--ink);text-decoration:none}
.main-nav a.active{color:var(--green)}

/* hero */
.hero{top:98px;height:509px;background:linear-gradient(180deg,#9fb3c3 0%,#7f95a8 45%,#8d9ba3 75%,#b9bdb8 100%)}
.hero-drone{position:absolute;left:520px;top:140px;width:580px;height:300px;background:radial-gradient(ellipse at center,#2b2f33 0%,#454b52 45%,rgba(120,135,150,0) 72%)}
.hero-copy{position:absolute;left:98px;top:250px;color:var(--white)}
.hero-copy h1{font-weight:300;font-size:52px;letter-spacing:1px;white-space:nowrap}
.hero-copy p{font-weight:400;font-size:30px;line-height:1.3;margin-top:14px}
.dots{position:absolute;display:flex;gap:6px}
.dots span{width:12px;height:12px;border:1px solid rgba(255,255,255,.9)}
.dots span.on{background:rgba(255,255,255,.9)}
.hero .dots{left:575px;top:464px}

/* about */
.about{top:607px;height:568px}
.section-title{position:absolute;left:0;width:1200px;text-align:center;font-weight:500;font-size:19px;letter-spacing:.5px}
.about .section-title{top:48px;color:var(--ink)}
.about-text{position:absolute;left:170px;width:860px;top:104px;text-align:center;font-family:'Open Sans',Arial,sans-serif;font-size:12.5px;line-height:25px;color:var(--muted)}
.team{position:absolute;top:227px;left:98px;display:flex;gap:9px}
.member{width:245px;height:264px;border:1px solid var(--line);padding:5px;text-align:center}
.member-photo{height:170px;border-radius:4px}
.member h3{font-weight:500;font-size:19px;color:var(--green);margin-top:18px;white-space:nowrap}
.member p{font-size:16px;margin-top:8px;letter-spacing:.5px}

/* services */
.services{top:1175px;height:849px;background:linear-gradient(180deg,var(--blue-light) 0%,var(--blue-deep) 100%);color:var(--white)}
.services .section-title{top:54px}
.service{position:absolute;width:300px;text-align:center}
.service svg{display:block;margin:0 auto}
.service h3{font-weight:500;font-size:17px;margin-top:30px}
.service p{font-family:'Open Sans',Arial,sans-serif;font-size:11.5px;line-height:20px;margin-top:16px;opacity:.95}
.service a{display:inline-block;font-size:10px;color:var(--white);margin-top:12px;text-decoration:underline}
.services .dots{left:575px;top:802px}

/* contact */
.contact{top:2024px;height:449px}
.contact .section-title{top:50px;color:var(--green)}
.field{position:absolute;border:1px solid #d6d6d6;height:48px;font-size:12px;color:#999;padding:16px 16px;display:flex;justify-content:space-between}
.field svg{flex:none}
.btn-send{position:absolute;left:517px;top:347px;width:166px;height:45px;background:var(--green-btn);color:var(--white);font-weight:600;font-size:15px;letter-spacing:.5px;border:0;border-radius:2px;font-family:'Raleway',Arial,sans-serif}

/* partners */
.partners{top:2473px;height:235px;background:#f3f3f3}
.partners .section-title{top:44px;color:var(--green);font-size:22px}
.partner-row{position:absolute;left:98px;top:113px;display:flex;gap:10px}
.partner-badge{width:192px;height:72px;background:var(--white);border:1px solid #e2e2e2;display:flex;align-items:center;justify-content:center}
.partner-badge span{width:140px;height:30px;background:#c9c9c9;border-radius:3px}
.arrow{position:absolute;top:134px;color:#999;font-size:22px}

/* footer */
.site-footer{top:2708px;height:282px;background:var(--footer);color:#ddd}
.footer-col{position:absolute;top:44px}
.footer-col h4{font-weight:500;font-size:15px;color:#e6e6e6;letter-spacing:.5px}
.footer-col ul{list-style:none;margin-top:30px;font-size:12px;line-height:34px;color:#ccc}
.footer-col ul.bullets li::before{content:"•";margin-right:12px}
.contact-line{display:flex;gap:14px;align-items:flex-start;font-size:12px;line-height:18px;color:#ccc;margin-top:14px}
.social{display:flex;gap:10px;margin-top:26px}
.social span{width:40px;height:40px;border:2px solid #eee;border-radius:50%;display:flex;align-items:center;justify-content:center;font-size:12px;font-weight:600;color:#eee}
.footer-bottom{position:absolute;left:0;top:2990px;width:1200px;height:76px;background:var(--footer-bottom);color:#ddd;font-size:12px;text-align:center;line-height:76px}
</style>
</head>
<body>

<header class="site-header">
  <div class="brand">
    <div class="brand-mark"></div>
    <div>
      <div class="brand-name">TORNWICK<br>AVIATION</div>
      <div class="brand-tag">Proven Leaders. Expert Solutions.</div>
    </div>
  </div>
  <nav class="main-nav">
    <a class="active" href="#">HOME</a><a href="#">ABOUT US</a><a href="#">SERVICES</a><a href="#">CAPABILITIES</a><a href="#">PARTNERS</a><a href="#">BLOG</a><a href="#">CONTACT US</a>
  </nav>
</header>

<section class="hero" role="img" aria-label="Aerial survey drone hovering over a misty hill landscape">
  <div class="hero-drone"></div>
  <div class="hero-copy">
    <h1>TORNWICK AVIATION</h1>
    <p>we are an aerial survey<br>drone company.</p>
  </div>
  <div class="dots"><span class="on"></span><span></span><span></span></div>
</section>

<section class="about">
  <h2 class="section-title">ABOUT US</h2>
  <p class="about-text">No his alii solum, vis iuvaret mentitum at. Cum alia esse te, solum munere consequuntur pro in. Mucius appetere iudicabit ei vix. Posidonium constituam vix in, est purto aperiri suscipit et, usu ut case posse. At agam tempor has, modo fuisset sea an. Quando saperet pro id, ex nam quod officiis. Legimus appetere eum cu, illum albucius mandamus eu duo.</p>
  <div class="team">
    <div class="member"><div class="member-photo" role="img" aria-label="Portrait of Maren Holt" style="background:linear-gradient(135deg,#e8edf2,#b9c6d1)"></div><h3>Maren Holt</h3><p>CEO</p></div>
    <div class="member"><div class="member-photo" role="img" aria-label="Portrait of Dale Whitcomb" style="background:linear-gradient(135deg,#dfe6ec,#aab7c2)"></div><h3>Dale Whitcomb</h3><p>PRESIDENT</p></div>
    <div class="member"><div class="member-photo" role="img" aria-label="Portrait of Rowan at the office" style="background:linear-gradient(135deg,#6e6a66,#c9bfb4)"></div><h3>Rowan</h3><p>DIRECTOR OF GIS</p></div>
    <div class="member"><div class="member-photo" role="img" aria-label="Portrait of Peter Lindqvist by office towers" style="background:linear-gradient(135deg,#5d7da0,#2e3f55)"></div><h3>Peter Lindqvist</h3><p>PARTNER</p></div>
  </div>
</section>

<section class="services">
  <h2 class="section-title">OUR SERVICES</h2>

  <div class="service" style="left:116px;top:130px">
    <svg width="143" height="143" viewBox="0 0 143 143"><circle cx="71.5" cy="71.5" r="68" fill="none" stroke="#fff" stroke-width="4"/><path d="M71 98V52M71 66c-10-4-16-12-16-22 10 2 16 10 16 22zM71 66c10-4 16-12 16-22-10 2-16 10-16 22zM71 84c-12-3-20-12-20-24 12 2 20 11 20 24zM71 84c12-3 20-12 20-24-12 2-20 11-20 24z" fill="#fff" stroke="#fff" stroke-width="3"/></svg>
    <h3>Precision Agriculture</h3>
    <p>At agam tempor has, modo fuisset sea an.<br>Quando saperet pro id, ex nam quod officiis.<br>Legimus appetere eum cu, illum</p>
    <a href="#">view more</a>
  </div>
  <div class="service" style="left:449px;top:130px">
    <svg width="143" height="143" viewBox="0 0 143 143"><circle cx="71.5" cy="71.5" r="68" fill="none" stroke="#fff" stroke-width="4"/><g fill="#fff"><ellipse cx="71.5" cy="50" rx="22" ry="8"/><rect x="49.5" y="56" width="44" height="10" rx="4"/><rect x="49.5" y="69" width="44" height="10" rx="4"/><rect x="49.5" y="82" width="44" height="10" rx="4"/></g></svg>
    <h3>FLLIR/IR</h3>
    <p>At agam tempor has, modo fuisset sea an.<br>Quando saperet pro id, ex nam quod officiis.<br>Legimus appetere eum cu, illum</p>
    <a href="#">view more</a>
  </div>
  <div class="service" style="left:786px;top:130px">
    <svg width="143" height="143" viewBox="0 0 143 143"><circle cx="71.5" cy="71.5" r="68" fill="none" stroke="#fff" stroke-width="4"/><path d="M71.5 88c-12-14-18-23-18-32a18 18 0 0 1 36 0c0 9-6 18-18 32z" fill="none" stroke="#fff" stroke-width="4"/><circle cx="71.5" cy="56" r="6" fill="#fff"/><ellipse cx="71.5" cy="92" rx="20" ry="5" fill="none" stroke="#fff" stroke-width="3"/></svg>
    <h3>GIS &amp; Mapping</h3>
    <p>At agam tempor has, modo fuisset sea an.<br>Quando saperet pro id, ex nam quod officiis.<br>Legimus appetere eum cu, illum</p>
    <a href="#">view more</a>
  </div>

  <div class="service" style="left:116px;top:471px">
    <svg width="143" height="143" viewBox="0 0 143 143"><circle cx="71.5" cy="71.5" r="68" fill="none" stroke="#fff" stroke-width="4"/><g fill="none" stroke="#fff" stroke-width="3"><rect x="64" y="64" width="15" height="15"/><path d="M64 64 52 52M79 64l12-12M64 79 52 91M79 79l12 12"/><circle cx="48" cy="48" r="8"/><circle cx="95" cy="48" r="8"/><circle cx="48" cy="95" r="8"/><circle cx="95" cy="95" r="8"/></g></svg>
    <h3>Video &amp; Still Images</h3>
    <p>At agam tempor has, modo fuisset sea an.<br>Quando saperet pro id, ex nam quod officiis.<br>Legimus appetere eum cu, illum</p>
    <a href="#">view more</a>
  </div>
  <div class="service" style="left:449px;top:471px">
    <svg width="143" height="143" viewBox="0 0 143 143"><circle cx="71.5" cy="71.5" r="68" fill="none" stroke="#fff" stroke-width="4"/><g fill="none" stroke="#fff" stroke-width="6"><path d="M60 100V46h14a12 12 0 0 1 0 24H60"/><circle cx="78" cy="80" r="18"/></g></svg>
    <h3>Section 333 Exemptions</h3>
    <p>At agam tempor has, modo fuisset sea an.<br>Quando saperet pro id, ex nam quod officiis.<br>Legimus appetere eum cu, illum</p>
    <a href="#">view more</a>
  </div>
  <div class="service" style="left:786px;top:471px">
    <svg width="143" height="143" viewBox="0 0 143 143"><circle cx="71.5" cy="71.5" r="68" fill="none" stroke="#fff" stroke-width="4"/><rect x="50" y="50" width="43" height="43" rx="5" fill="#fff"/><circle cx="67" cy="77" r="9" fill="none" stroke="var(--blue-deep)" stroke-width="4"/><path d="M73 70l10-10M76 60h7v7" fill="none" stroke="var(--blue-deep)" stroke-width="4"/></svg>
    <h3>Public Services:</h3>
    <p>At agam tempor has, modo fuisset sea an.<br>Quando saperet pro id, ex nam quod officiis.<br>Legimus appetere eum cu, illum</p>
    <a href="#">view more</a>
  </div>

  <div class="dots"><span class="on"></span><span></span><span></span></div>
</section>

<section class="contact">
  <h2 class="section-title">CONTACT US</h2>
  <div class="field" style="left:98px;top:126px;width:495px">First &amp; Last name
    <svg width="18" height="18" viewBox="0 0 18 18"><circle cx="9" cy="5" r="4" fill="#ccc"/><path d="M1 18c0-5 4-8 8-8s8 3 8 8z" fill="#ccc"/></svg></div>
  <div class="field" style="left:98px;top:189px;width:495px">Phone No.
    <svg width="18" height="18" viewBox="0 0 18 18"><path d="M3 1l4 1 1 4-2 2c1 2 3 4 5 5l2-2 4 1 1 4-2 1C8 17 1 10 1 3z" fill="#ccc"/></svg></div>
  <div class="field" style="left:98px;top:253px;width:495px">Email Id *
    <svg width="20" height="16" viewBox="0 0 20 16"><rect x="1" y="2" width="18" height="12" fill="none" stroke="#ccc" stroke-width="1.5"/><path d="M1 2l9 7 9-7" fill="none" stroke="#ccc" stroke-width="1.5"/></svg></div>
  <div class="field" style="left:623px;top:126px;width:477px">Address
    <svg width="20" height="18" viewBox="0 0 20 18"><path d="M1 17V6l6-4v4l6-4v15z" fill="#ccc"/><rect x="14" y="1" width="5" height="16" fill="#ccc"/></svg></div>
  <div class="field" style="left:623px;top:189px;width:477px;height:111px;align-items:flex-start;padding-top:12px">your message
    <svg width="20" height="16" viewBox="0 0 20 16" style="margin-top:10px"><rect x="1" y="2" width="18" height="12" fill="none" stroke="#ccc" stroke-width="1.5"/><path d="M1 2l9 7 9-7" fill="none" stroke="#ccc" stroke-width="1.5"/></svg></div>
  <button class="btn-send">SEND MESSAGE</button>
</section>

<section class="partners">
  <h2 class="section-title">OUR PARTNERS</h2>
  <span class="arrow" style="left:38px">‹</span>
  <div class="partner-row">
    <div class="partner-badge"><span></span></div>
    <div class="partner-badge"><span></span></div>
    <div class="partner-badge"><span></span></div>
    <div class="partner-badge"><span></span></div>
    <div class="partner-badge"><span></span></div>
  </div>
  <span class="arrow" style="left:1128px">›</span>
</section>

<footer class="site-footer">
  <div class="footer-col" style="left:98px;width:300px">
    <h4>CONTACT US</h4>
    <div class="contact-line" style="margin-top:34px"><svg width="16" height="14" viewBox="0 0 16 14"><path d="M8 0 0 7h2v7h4V9h4v5h4V7h2z" fill="var(--blue)"/></svg><span>2207 W. 64th Terrace | Linwood Park<br>KS 66031</span></div>
    <div class="contact-line" style="margin-top:22px"><svg width="16" height="18" viewBox="0 0 16 18"><rect x="3" y="0" width="10" height="18" rx="2" fill="var(--blue)"/></svg><span>Call us on : (913)555-0142</span></div>
    <div class="contact-line" style="margin-top:22px"><svg width="16" height="12" viewBox="0 0 16 12"><rect x="1" y="1" width="14" height="10" fill="none" stroke="var(--blue)" stroke-width="1.5"/><path d="M1 1l7 6 7-6" fill="none" stroke="var(--blue)" stroke-width="1.5"/></svg><span>info@tornwickaviation.com</span></div>
  </div>
  <div class="footer-col" style="left:415px">
    <h4>QUICK LINKS</h4>
    <ul class="bullets"><li>vim modo ipsum</li><li>vim modo ipsum</li><li>vim modo ipsum</li><li>vim modo ipsum</li></ul>
  </div>
  <div class="footer-col" style="left:650px">
    <h4>ABOUT</h4>
    <ul class="bullets"><li>Maren Holt – CEO</li><li>Dale Whitcomb – President</li><li>Rowan – Director of GIS</li><li>Peter Lindqvist – Partner</li></ul>
  </div>
  <div class="footer-col" style="left:910px">
    <h4>OUR CLIENTS</h4>
    <div class="social"><span>FB</span><span>TW</span><span>IG</span></div>
  </div>
</footer>
<div class="footer-bottom">All Rights Reserved . copyrights2016@tornwickaviation.com</div>

</body>
</html>
```